Steadfast Field Crews

We are a underground coal mining labour hire company, needing a website that links into our online payroll (www.wagelinkr.com.au) and also need to have job applications page that is a preform with drop down menu,s with answers or check boxes. We would also need a 3 tier administration access for access to different files.
We are looking for an ongoing relationship with future app integration

Reason: There are a few more designs to come and I'm out at the mine for another week

Industry/Entity Type

Coal Mining

```html
<!DOCTYPE html>
<html lang="en">
<head>
<meta charset="utf-8">
<title>Steadfast Field Crews</title>
<link rel="stylesheet" href="https://fonts.googleapis.com/css2?family=Source+Sans+3:wght@400;600&display=swap">
<style>
:root{
  --black:#000;
  --panel:#0b0b0b;
  --date-box:#2b2c2f;
  --orange:#f0841c;
  --orange-dark:#e8760f;
  --white:#fff;
  --body-text:#454545;
  --muted:#9a9a9a;
  --brand-blue:#7f84d8;
  --social:#8a8a8a;
}
*{box-sizing:border-box;margin:0;padding:0}
html,body{width:1200px;height:895px;overflow:hidden;background:var(--white)}
body{position:relative;font-family:"Source Sans 3",Arial,sans-serif;color:var(--white)}
a{color:inherit;text-decoration:none}

.site-header{position:absolute;left:0;top:0;width:1200px;height:129px;background:var(--black)}
.search{position:absolute;left:866px;top:19px;width:202px;height:36px;border-radius:18px;
  background:linear-gradient(#fff,#dcdcdc);color:#555;font-size:13px;line-height:36px;padding-left:17px}
.search svg{position:absolute;right:13px;top:8px}
.main-nav{position:absolute;right:129px;top:78px;font-size:17px;white-space:nowrap}
.main-nav a{margin:0 3px}
.main-nav .sep{color:#bbb;font-size:14px;margin:0 2px}
.main-nav .current{color:var(--orange)}

.hero{position:absolute;left:0;top:129px;width:1200px;height:407px;
  background:linear-gradient(180deg,#6f7d8c 0%,#b9ab90 22%,#4e4a42 30%,#5d5a54 55%,#3f3b35 75%,#7a5e45 100%)}
.hero-title{position:absolute;left:382px;top:96px;font-size:27px;color:var(--white)}
.slider-dots{position:absolute;left:379px;top:371px;display:flex;gap:9px}
.slider-dots span{width:12px;height:10px;border-radius:50%;background:var(--white)}
.slider-dots .active{background:var(--black)}

.brand-panel{position:absolute;left:100px;top:0;width:248px;height:329px;background:var(--panel);
  display:flex;flex-direction:column;align-items:center;justify-content:center;gap:14px}
.brand-panel .mark{width:40px;height:40px;border-radius:50%;background:var(--orange)}
.brand-panel .name{font-size:22px;font-weight:600;color:var(--white);text-align:center;line-height:1.2}

.content{position:absolute;left:0;top:536px;width:1200px;height:242px;background:var(--white)}
.welcome{position:absolute;left:373px;top:16px;width:700px}
.welcome h1{font-size:29px;font-weight:400;color:var(--orange);line-height:1.2;margin-bottom:9px}
.welcome p{font-size:13.3px;line-height:16.5px;color:var(--body-text);margin-bottom:16px}
.btn-readmore{position:absolute;left:373px;top:181px;width:92px;height:33px;border-radius:17px;
  background:linear-gradient(var(--orange),var(--orange-dark));color:var(--white);font-size:13px;
  line-height:33px;text-align:center}

.news{position:absolute;left:100px;top:457px;width:248px;height:321px;background:var(--panel)}
.news h2{position:absolute;left:25px;top:12px;font-size:27px;font-weight:400;color:var(--orange)}
.news-item{position:absolute;left:10px;width:222px;height:59px}
.news-date{position:absolute;left:0;top:0;width:43px;height:59px;background:var(--date-box);
  text-align:center;font-size:14px;line-height:1.3;padding-top:6px}
.news-date b{display:block;font-weight:400;font-size:17px}
.news-text{position:absolute;left:50px;top:10px;width:175px;font-size:11px;line-height:14.5px}
.news-more{position:absolute;right:0;top:50px;font-size:13px;color:var(--orange)}

.site-footer{position:absolute;left:0;top:778px;width:1200px;height:117px;background:var(--black)}
.footer-brand{position:absolute;left:115px;top:24px;display:flex;align-items:center;gap:8px}
.footer-brand .mark{width:36px;height:36px;background:var(--brand-blue)}
.footer-brand .name{font-size:34px;color:var(--brand-blue);line-height:1}
.copyright{position:absolute;left:127px;top:87px;font-size:12px;color:var(--muted)}
.footer-nav{position:absolute;right:137px;top:29px;font-size:13px;white-space:nowrap}
.footer-nav a{margin:0 2px}
.footer-nav .sep{color:#bbb;margin:0 1px}
.footer-nav .current{color:var(--orange)}
.social{position:absolute;left:964px;top:68px;display:flex;gap:10px}
.social a{width:25px;height:25px;border-radius:4px;background:linear-gradient(#a5a5a5,#6d6d6d)}
.page-code{position:absolute;left:1120px;top:66px;font-size:12px;color:#bbb}
</style>
</head>
<body>
<header class="site-header">
  <div class="search">Search
    <svg width="20" height="20" viewBox="0 0 20 20"><circle cx="8" cy="8" r="6.5" fill="none" stroke="#666" stroke-width="2"/><line x1="12.5" y1="12.5" x2="18" y2="18" stroke="#666" stroke-width="2.4" stroke-linecap="round"/></svg>
  </div>
  <nav class="main-nav">
    <a class="current" href="#">Home</a><span class="sep">::</span>
    <a href="#">Apply for position</a><span class="sep">::</span>
    <a href="#">Pay Portal</a><span class="sep">::</span>
    <a href="#">Download</a><span class="sep">::</span>
    <a href="#">Mission</a><span class="sep">::</span>
    <a href="#">About us</a><span class="sep">::</span>
    <a href="#">Contact us</a>
  </nav>
</header>

<section class="hero" role="img" aria-label="Open-cut coal mine landscape with two workers in hard hats and high-visibility vests looking across the pit">
  <div class="hero-title">Steadfast Field Crews</div>
  <div class="slider-dots"><span></span><span></span><span></span><span class="active"></span></div>
</section>

<div class="brand-panel">
  <span class="mark"></span>
  <span class="name">Steadfast<br>Field Crews</span>
</div>

<main class="content">
  <div class="welcome">
    <h1>Welcome</h1>
    <p>We are Kestrel Ridge Pty Ltd trading as Steadfast Field Crews, we are experienced in ground consolidation in underground coal mines, in short when they collapse or cave in we come in with chemical pumps and stabilise the ground or fill cavities which will then allow for the mining process to continue. We also do general mine labor as well.</p>
    <p>We are a labor hire company for major mining services company, we offer labor solutions in New South Wales and Queensland in the underground coal mines.</p>
  </div>
  <a class="btn-readmore" href="#">Readmore</a>
</main>

<aside class="news">
  <h2>News</h2>
  <div class="news-item" style="top:64px">
    <div class="news-date">Jan<b>01</b></div>
    <p class="news-text">Lorem Ipsum is simply dummy text of the printing and typesetting industry.</p>
    <a class="news-more" href="#">read more</a>
  </div>
  <div class="news-item" style="top:145px">
    <div class="news-date">Jan<b>01</b></div>
    <p class="news-text">Lorem Ipsum is simply dummy text of the printing and typesetting industry.</p>
    <a class="news-more" href="#">read more</a>
  </div>
  <div class="news-item" style="top:226px">
    <div class="news-date">Jan<b>01</b></div>
    <p class="news-text">Lorem Ipsum is simply dummy text of the printing and typesetting industry.</p>
    <a class="news-more" href="#">read more</a>
  </div>
</aside>

<footer class="site-footer">
  <div class="footer-brand"><span class="mark"></span><span class="name">wagelinkr</span></div>
  <div class="copyright">© 2014.www.companyname.com</div>
  <nav class="footer-nav">
    <a class="current" href="#">Home</a><span class="sep">::</span>
    <a href="#">Apply for position</a><span class="sep">::</span>
    <a href="#">Pay Portal</a><span class="sep">::</span>
    <a href="#">Download</a><span class="sep">::</span>
    <a href="#">Mission</a><span class="sep">::</span>
    <a href="#">About us</a><span class="sep">::</span>
    <a href="#">Contact us</a>
  </nav>
  <div class="social">
    <a href="#" aria-label="Social network link"></a>
    <a href="#" aria-label="Social network link"></a>
    <a href="#" aria-label="Social network link"></a>
  </div>
  <div class="page-code">M1</div>
</footer>
</body>
</html>
```